Website for new dental office

I am Dr. Colin Ashford and am building a new dental practice. I specialize in general dentistry. I am young and have a higher end dental practice incorporating very new technologies and would like my website to reflect that. As many dental patients are older, the website must be very easy to navigate. I would like patients to be able to request appointments, and will eventually add on patient information forms (the health history, etc, that you normally fill out in the practice) from my practice management software, so leave an area for that.

Industry/Entity Type

Building

```html
<!DOCTYPE html>
<html lang="en">
<head>
<meta charset="utf-8">
<title>Ashford Dental Clinic</title>
<link href="https://fonts.googleapis.com/css2?family=Source+Sans+3:ital,wght@0,400;0,600;1,400&display=swap" rel="stylesheet">
<style>
:root{
  --green:#6cb32a;
  --green-btn:#74c02e;
  --ink:#3c3c3c;
  --text:#666;
  --muted:#8a8a8a;
  --band:#f4f4f4;
  --line:#e2e2e2;
  --panel:#4a4a4a;
  --white:#fff;
}
*{margin:0;padding:0;box-sizing:border-box}
html,body{width:788px;height:1200px;overflow:hidden;background:var(--white)}
body{position:relative;font-family:"Source Sans 3",Arial,sans-serif;color:var(--text)}
.abs{position:absolute}

.hero{left:0;top:0;width:788px;height:474px;
  background:radial-gradient(ellipse at 50% 40%,#8aa6c6 0%,#c9d3dc 35%,#e4e6e6 65%,#d8dcd6 100%)}
.header{left:86px;top:14px;width:616px;height:76px;background:var(--white);box-shadow:0 1px 3px rgba(0,0,0,.2)}
.brand{left:14px;top:18px;display:flex;align-items:center;gap:8px}
.brand-mark{width:30px;height:30px;background:var(--green);border-radius:4px}
.brand-name{font-size:22px;color:var(--green);line-height:1}
.brand-name small{display:block;font-size:15px;color:var(--ink);margin-top:3px}
.call{left:366px;top:18px;font-size:10px;color:var(--ink);display:flex;align-items:center;gap:5px}
.call b{font-weight:400;font-size:14px;color:var(--green)}
.socials{left:518px;top:17px;display:flex;gap:5px}
.socials span{width:18px;height:18px;border:1px solid #ccc;border-radius:50%;background:#f7f7f7}
.nav{right:14px;top:52px;display:flex;font-size:9.5px;color:var(--ink)}
.nav a{color:inherit;text-decoration:none;padding:0 10px;border-left:1px solid #999;line-height:10px}
.nav a:first-child{border:0;color:var(--green)}
.arrow{width:34px;height:34px;border-radius:50%;background:rgba(60,60,60,.75);top:236px}
.caption{left:102px;top:379px;width:588px;height:73px;background:rgba(245,245,245,.85);padding:16px 26px;font-size:14px;line-height:21px;color:#555}
.caption b{font-weight:400;color:var(--green);font-size:19px}

.features{left:0;top:474px;width:788px;height:235px;background:var(--band)}
.feature{width:160px;top:51px;text-align:center}
.feature .disc{width:72px;height:72px;border-radius:50%;background:var(--white);margin:0 auto;box-shadow:0 1px 3px rgba(0,0,0,.12);display:flex;align-items:center;justify-content:center}
.feature h3{font-weight:400;font-size:12.5px;line-height:16px;color:var(--green);margin-top:14px;height:38px}
.feature .more{display:inline-block;margin-top:4px;background:var(--white);font-size:8px;color:var(--ink);padding:6px 10px;box-shadow:0 1px 2px rgba(0,0,0,.15)}

.about h2,.blog h2{font-weight:400;font-size:20px;color:var(--ink)}
.about{left:86px;top:738px;width:400px}
.about p{margin-top:10px;font-size:8.3px;line-height:16px;color:var(--text)}
.team-photo{left:506px;top:742px;width:196px;height:119px;background:linear-gradient(135deg,#b9c6cf,#eef0f0 50%,#9fb3c4)}

.lower{left:0;top:896px;width:788px;height:242px;background:var(--band)}
.blog{left:86px;top:922px;width:229px}
.blog .pager{position:absolute;right:0;top:6px;display:flex;gap:2px}
.blog .pager span{width:12px;height:11px;background:#888}
.avatar{left:0;top:37px;width:70px;height:70px;border-radius:50%;background:linear-gradient(#d9a57e,#f0d2bc);border:3px solid var(--white)}
.quote{left:90px;top:43px;width:140px;font-size:8.3px;line-height:14.5px;color:var(--text)}
.quote i{color:var(--green);font-size:14px;font-weight:600}
.blog .body{position:absolute;top:118px;font-size:8.3px;line-height:14.5px}
.blog .by{position:absolute;top:163px;font-size:8px;line-height:15px;color:var(--muted);font-style:italic}
.blog .by em{color:var(--green)}
.services{left:349px;top:922px;width:134px}
.services h2{font-weight:400;font-size:17px;color:var(--green)}
.services ul{list-style:none;margin-top:8px}
.services li{font-size:8.3px;color:var(--ink);height:24.5px;line-height:24px;border-bottom:1px solid var(--line);padding-left:13px;position:relative}
.services li:last-child{border:0}
.services li::before{content:"";position:absolute;left:1px;top:10px;border-left:4px solid var(--green);border-top:2.5px solid transparent;border-bottom:2.5px solid transparent}
.appt{left:506px;top:920px;width:196px;height:195px;background:var(--panel);padding:12px 11px}
.appt h2{font-weight:400;font-size:12px;color:var(--white)}
.field{background:var(--white);border-radius:2px;height:22px;margin-top:8px;font-size:7.5px;font-style:italic;color:#999;padding:6px 10px}
.appt .field:first-of-type{margin-top:12px}
.field.tall{height:51px}
.submit{position:absolute;right:11px;bottom:12px;width:58px;height:19px;background:var(--green-btn);color:var(--white);font-size:7.5px;font-weight:600;text-align:center;line-height:19px;border-radius:2px}

.copy{left:86px;top:1166px;font-size:8.3px;color:var(--muted)}
.copy span{color:var(--green)}
.top{left:676px;top:1158px;width:26px;height:27px;background:#999;color:var(--white);font-size:6.5px;text-align:center;padding-top:11px}
</style>
</head>
<body>
<div class="abs hero" role="img" aria-label="Photograph of a masked dentist holding a dental mirror and probe"></div>
<header class="abs header">
  <div class="abs brand"><span class="brand-mark"></span><div class="brand-name">ASHFORD<small>Dental Clinic</small></div></div>
  <div class="abs call">
    <svg width="16" height="16" viewBox="0 0 16 16"><circle cx="8" cy="8" r="7.5" fill="none" stroke="#bbb"/><path d="M5.5 4.5l1.5 1.2-.6 1.3c.5 1 1.3 1.9 2.4 2.5l1.3-.7 1.3 1.5-1.2 1.2c-2.6-.3-5-2.8-5.2-5.6z" fill="#999"/></svg>
    Call Us : <b>(012) 555 0147</b>
  </div>
  <div class="abs socials"><span></span><span></span><span></span><span></span></div>
  <nav class="abs nav"><a href="#">Home</a><a href="#">About Us</a><a href="#">Our Service</a><a href="#">Blog</a><a href="#">Our Dentist</a><a href="#">Contact Us</a></nav>
</header>
<svg class="abs arrow" style="left:67px" viewBox="0 0 34 34"><path d="M19 11l-6 6 6 6" fill="none" stroke="#fff" stroke-width="1.5"/></svg>
<svg class="abs arrow" style="left:687px" viewBox="0 0 34 34"><path d="M15 11l6 6-6 6" fill="none" stroke="#fff" stroke-width="1.5"/></svg>
<div class="abs caption"><b>Dr. Colin Ashford</b> is specialised in general dentistry. He provides higher end dental practice incorporating very new technologies.</div>

<section class="abs features">
  <div class="abs feature" style="left:78px">
    <div class="disc"><svg width="32" height="32" viewBox="0 0 32 32"><circle cx="16" cy="16" r="14" fill="none" stroke="#777" stroke-width="2"/><circle cx="11" cy="13" r="1.8" fill="#777"/><circle cx="21" cy="13" r="1.8" fill="#777"/><path d="M9 18c2 5 12 5 14 0" fill="none" stroke="#777" stroke-width="2"/></svg></div>
    <h3>Specialised in Healthy &amp; Protective Smiles</h3><span class="more">Read More</span>
  </div>
  <div class="abs feature" style="left:235px">
    <div class="disc"><svg width="32" height="32" viewBox="0 0 32 32"><path d="M8 6h4v8l4 10H4l4-10z M19 8h4v7l4 9H15l4-9z" fill="#888"/></svg></div>
    <h3>Diagnosing Unique Problem &amp; Oral Surgery</h3><span class="more">Read More</span>
  </div>
  <div class="abs feature" style="left:393px">
    <div class="disc"><svg width="32" height="32" viewBox="0 0 32 32"><rect x="3" y="9" width="26" height="18" rx="2" fill="#777"/><rect x="12" y="5" width="8" height="5" fill="none" stroke="#777" stroke-width="2"/><path d="M14 14h4v3h3v4h-3v3h-4v-3h-3v-4h3z" fill="#fff"/></svg></div>
    <h3>Our Highest Standard for Dental Treatments</h3><span class="more">Read More</span>
  </div>
  <div class="abs feature" style="left:550px">
    <div class="disc"><svg width="32" height="32" viewBox="0 0 32 32"><path d="M20 3l5 4-9 12-5-4z M10 16l5 4-5 9-4-3z" fill="#777"/></svg></div>
    <h3>Highly Qualified &amp; Experienced Consultant</h3><span class="more">Read More</span>
  </div>
</section>

<section class="abs about">
  <h2>About Us</h2>
  <p>Lorem ipsum dolor sit amet, consectetur adipisicing elit, sed do eiusmod tempor incididunt ut labore etu dolore magna aliqua. Ut enim ad minim veniam, quis nostrud exercitation ullamco laboris nisi ut aliquipe ea commodo consequat. Duis aute irure dolor in reprehenderit in voluptate velit esse cillum dolore euse fugiat nulla pariatur. Lorem ipsum dolor sit amet, consectetur adipisicing elit, sed do eiusmod temporuei incididunt ut labore et dolore magna aliqua.</p>
</section>
<div class="abs team-photo" role="img" aria-label="Photograph of a smiling medical team in white coats"></div>

<div class="abs lower"></div>
<section class="abs blog">
  <h2>Blog Post</h2>
  <div class="pager"><span></span><span></span></div>
  <div class="abs avatar" role="img" aria-label="Portrait photograph of the patient"></div>
  <p class="abs quote"><i>“</i> Vsanamet, consect etur, adipisciu velits quia nqueius erynasas setyera krscad eras tayse squrem ipsum que sanamet, consect etur.</p>
  <p class="body">Vsanamet, consect etur, adipisci velitsed quia nqueiusesoue erynasas setyera krscaderas tayse squrem ipsum quia.</p>
  <p class="by"><em>by Nora Castell</em><br>from Newyork city</p>
</section>
<section class="abs services">
  <h2>Our Services</h2>
  <ul>
    <li>Vsanamet, consect etuou</li>
    <li>Adipisci velitsed quia setyera</li>
    <li>Queius erynasas setyera</li>
    <li>Tayse squrem ipsum quia</li>
    <li>Vsanamet, consect etuousr</li>
    <li>Adipisci velitsed quia setyera</li>
    <li>Queius erynasas setyera</li>
  </ul>
</section>
<section class="abs appt">
  <h2>Make an Appointment</h2>
  <div class="field">Enter your Name..</div>
  <div class="field">Enter your Email..</div>
  <div class="field tall">Leave comment..</div>
  <div class="submit">SUBMIT</div>
</section>

<footer>
  <p class="abs copy">Copyright 2014 © <span>Ashford Dental Clinic</span>. All rights reserved</p>
  <div class="abs top">↑<br>TOP</div>
</footer>
</body>
</html>
```